Design and Renovation Company Luxury Business Card

I want to create a luxury business card for a Design and Renovation Firm . We will use our current logo. The company name is 528BUILDA. We do not want anything standard. We need a very unique concept.
Please see uploaded inspiration. I really like the textured paper option. I would like the card to be thick with debossing, and/or embossing options. The logo has orange in it but I would like to see the card with and without the orange. I think the orange may make the company feel less high-end. The goal is to elevate the logo not match its vibe per se of the logo. We want something very unique, not standard at all!
I would like a space for :
Logo,
Name,
Position,
Email,
Office number,
Website Address,
Business Address,
Thank you!
Have fun!
Target Market(s)
Home owners Age 35 +
Industry/Entity Type
Design and Renovation
Contact Information for Business Card
Logo, Name, Position, Email, Office number, Website Address, Business Address,.
Colors
Designer to choose colors to be used in the design.
Requirements
Must have
- A luxury designer feel. Must be black or dark grey but open to other luxury ideas.
Nice to have
- Gold, silver, black embossing or debossing. Textured paper design.
Should not have
- A cheap look and feel.

```html
<!DOCTYPE html>
<html lang="en">
<head>
<meta charset="utf-8">
<title>528BUILDA Business Card</title>
<link rel="stylesheet" href="https://fonts.googleapis.com/css2?family=Montserrat:wght@400;500;700&display=swap">
<style>
  :root {
    --backdrop: #6b6b6a;
    --card-dark: #181818;
    --accent: #f7941f;
    --ink-light: #ffffff;
  }
  * { margin: 0; padding: 0; box-sizing: border-box; }
  html, body {
    width: 1200px; height: 801px; overflow: hidden;
    background: var(--backdrop);
    font-family: "Montserrat", sans-serif;
  }
  .stage {
    position: relative; width: 1200px; height: 801px;
    display: flex; align-items: center; justify-content: center; gap: 50px;
  }
  .card {
    position: relative; width: 525px; height: 300px;
  }
  .card--front {
    background: var(--card-dark);
    border-bottom: 2px solid var(--accent);
  }
  .card--back {
    background: var(--accent);
    display: flex; align-items: center; justify-content: center;
  }
  .brand-name {
    font-family: "Montserrat", sans-serif;
    font-weight: 400;
    letter-spacing: 0;
  }
  .card--front .brand-name {
    position: absolute; left: 40px; top: 132px;
    font-size: 26px; color: var(--ink-light);
  }
  .card--back .brand-name {
    font-size: 30px; color: var(--card-dark);
  }
  .divider {
    position: absolute; left: 262px; top: 56px;
    width: 1.5px; height: 188px; background: var(--accent);
  }
  .contact {
    position: absolute; left: 285px; top: 52px;
    color: var(--ink-light); font-size: 12.5px; line-height: 1.55;
  }
  .contact__name {
    color: var(--accent); font-weight: 700; font-size: 19px;
    letter-spacing: 0.5px; line-height: 1.2;
  }
  .contact__role { margin-bottom: 8px; }
  .contact__address { margin-bottom: 8px; }
  .contact__line { display: flex; align-items: center; gap: 8px; }
  .contact__icon { width: 12px; height: 12px; flex: none; }
</style>
</head>
<body>
<main class="stage">
  <section class="card card--front" aria-label="Card front">
    <p class="brand-name">528BUILDA</p>
    <span class="divider"></span>
    <div class="contact">
      <p class="contact__name">DANIEL CARTER</p>
      <p class="contact__role">Managing Director</p>
      <p class="contact__address">Your address, City<br>State, Zip 1234</p>
      <p class="contact__line">
        <svg class="contact__icon" viewBox="0 0 12 12" aria-hidden="true"><path fill="#f7941f" d="M2.5 1l2 2.2-1 1.3a6 6 0 0 0 4 4l1.3-1 2.2 2-1.2 1.5C5.5 11 1 6.5 1 2.2z"/></svg>
        555 014 288
      </p>
      <p class="contact__line">
        <svg class="contact__icon" viewBox="0 0 12 12" aria-hidden="true"><rect x="0.5" y="2.5" width="11" height="7.5" fill="#f7941f"/><path d="M0.8 2.8L6 7l5.2-4.2" stroke="#181818" fill="none"/></svg>
        info@528builda.com
      </p>
      <p class="contact__line">
        <svg class="contact__icon" viewBox="0 0 12 12" aria-hidden="true"><circle cx="6" cy="6" r="5.5" fill="#f7941f"/><path d="M0.5 6h11M6 0.5c-2.5 3-2.5 8 0 11M6 0.5c2.5 3 2.5 8 0 11" stroke="#181818" stroke-width="0.8" fill="none"/></svg>
        www.528builda.com
      </p>
    </div>
  </section>
  <section class="card card--back" aria-label="Card back">
    <p class="brand-name">528BUILDA</p>
  </section>
</main>
</body>
</html>
```